[Book title] Chasing a Ledgerless Tomorrow: Plumbook, Tessaria & the Dawn of a Faithless Ag...

Book Title: Chasing a Ledgerless Tomorrow
Subtitle: Plumbook, Tessaria & the Dawn of a Faithless Age
Author: Weilong Guo

We need a book cover for a book to be published through Borvent QPL. The title of the book describes three subjects which make up the three chapters of the book. The book is about 130 pages long. We would like to see designs that reflect the three subject matters in a minimalistic style. We would also like to see that the graphics used are intuitive.

In addition, we have some testimonies and passages to be put on the backside of the cover. Please include them in the design:

Chasing a Ledgerless Tomorrow gives an informative overview of the international competition in money today. With the competition in the digitization of money between Tessaria, Plumbook, the U.S. and other various actors mounting in the background, Weilong Guo aims to provide readers with insights into how a new world financial order is changing our life without us noticing.

“This book weaves together the future of finance and the international dynamics of it in a way that was never done before. With a detailed telling of the recent history of the fintech push in Tessaria and Plumbook’s development in the U.S., Guo reveals the underlying forces behind the digitalization of money.“
Mira Tan, Manager of Coinvale Society in China Area

“The digitization of money is has transformed from an individual, online project into an institutional, national project. With powerful state actors and multinational corporations behind the scene, everyone should pay attention to where this technological transformation is leading us.”
Ko Pell, Author of Unwinding Coinvale

Industry/Entity Type

Fintech

Requirements
Must have
• Minimalistic illustration that shows the subject
No more than two text color
Not crowded design (please reference my uploaded files)

[Graphics]
Theme: digitalization of money/ mobile payments/ paperless money/ crypto
Inspiration: please consider creating a design that shows the digitalization of money and mobile payment (for inspiration refer to one of the dollar sign and dollar bill pictures we uploaded)
IMPORTANT: please make the bill currency-neutral; that is the graphic should not be solely based on one currency. For designs with currency signs, please make sure to represent both $ and ¥
Should not have
• Stock image as background

```html
<!DOCTYPE html>
<html lang="en">
<head>
<meta charset="utf-8">
<title>Chasing a Ledgerless Tomorrow — Weilong Guo</title>
<link rel="stylesheet" href="https://fonts.googleapis.com/css2?family=Montserrat:wght@300;500;700&display=swap">
<style>
  :root {
    --cover-blush: #ebb9aa;
    --ink: #0d0d0d;
    --steel-light: #f4f4f4;
    --steel-mid: #cfcfcf;
    --steel-dark: #8e8e8e;
  }
  html, body {
    margin: 0;
    padding: 0;
    width: 849px;
    height: 1200px;
    overflow: hidden;
    background: var(--cover-blush);
  }
  .cover {
    position: relative;
    width: 849px;
    height: 1200px;
    background: var(--cover-blush);
    color: var(--ink);
    font-family: "Montserrat", sans-serif;
    overflow: hidden;
  }
  .title-main {
    position: absolute;
    top: 146px;
    left: 0;
    width: 100%;
    margin: 0;
    text-align: center;
    font-weight: 500;
    font-size: 136px;
    line-height: 1;
    letter-spacing: 1px;
  }
  .title-rest {
    position: absolute;
    top: 281px;
    left: 0;
    width: 100%;
    margin: 0;
    text-align: center;
    font-weight: 300;
    font-size: 43px;
    line-height: 51px;
    letter-spacing: 0.5px;
    text-transform: uppercase;
  }
  .timepiece-art {
    position: absolute;
    left: 248px;
    top: 385px;
    width: 332px;
    height: 432px;
  }
  .subtitle {
    position: absolute;
    top: 836px;
    left: 0;
    width: 100%;
    margin: 0;
    text-align: center;
    font-weight: 700;
    font-size: 25px;
    line-height: 34px;
    letter-spacing: 2.5px;
    text-transform: uppercase;
  }
  .author {
    position: absolute;
    top: 1048px;
    left: 0;
    width: 100%;
    margin: 0;
    text-align: center;
    font-weight: 700;
    font-size: 42px;
    line-height: normal;
    letter-spacing: 17px;
    text-indent: 17px;
    text-transform: uppercase;
  }
</style>
</head>
<body>
  <main class="cover">
    <h1 class="title-main">CHASING</h1>
    <p class="title-rest">A Ledgerless<br>Tomorrow</p>

    <svg class="timepiece-art" viewBox="0 0 332 432" role="img" aria-label="Illustration of a silver stopwatch with a white dial, a crown and a side pusher, standing for the race toward digital money">
      <defs>
        <radialGradient id="steel-sheen" cx="42%" cy="55%" r="65%">
          <stop offset="0%" stop-color="var(--steel-light)"/>
          <stop offset="70%" stop-color="var(--steel-mid)"/>
          <stop offset="100%" stop-color="var(--steel-dark)"/>
        </radialGradient>
      </defs>
      <circle cx="165" cy="264" r="164" fill="url(#steel-sheen)"/>
    </svg>

    <p class="subtitle">Plumbook, Tessaria<br>&amp; the Dawn of<br>a Faithless Age</p>

    <p class="author">Weilong Guo</p>
  </main>
</body>
</html>
```